Vellisant - Quality health delivered at your door

Vellisant offers home and Community Based Services for adults who wish to continue live independently in their communities. We increase accessibility to health care, reduce health care delivery gap, reduce mortality and morbidity, reduce health while promoting healthy living in the comfort of our patients communities or homes.

We provide on site services and deliver high quality healthcare at your door. Our experienced physicians coordinate care with our certified nurse practitioners and provide chronic care management, physical therapy, rehabilitation and medications management.

Target Market(s)

Older population living in independent living facilities

Industry/Entity Type

Health Care

Contact Information for Business Card

Vellisant

Number of Pages Required

4 page

Font styles to use
Sans Serif

Colors

Designer to choose colors to be used in the design.

```html
<!DOCTYPE html>
<html lang="en">
<head>
<meta charset="utf-8">
<title>Vellisant - Quality health delivered at your door</title>
<link href="https://fonts.googleapis.com/css2?family=Open+Sans:wght@400;600;700&family=Arimo:wght@400;700&display=swap" rel="stylesheet">
<style>
:root{
  --green:#5b8113;
  --green-dark:#1f3a12;
  --orange:#f7941d;
  --ink:#2b2b2b;
  --muted:#6d6d6d;
  --line:#dcdcdc;
  --soft:#f4f4f4;
  --band:#37444b;
  --white:#ffffff;
}
*{box-sizing:border-box;margin:0;padding:0}
html,body{width:1200px;height:2507px;overflow:hidden;background:var(--white)}
body{position:relative;font-family:"Arimo",Arial,sans-serif;color:var(--ink)}
.abs{position:absolute}

/* header */
.topline{left:0;top:0;width:1200px;height:5px;background:var(--orange)}
.call{left:132px;top:28px;display:flex;align-items:center;gap:14px}
.call-label{font-size:13px;color:var(--muted)}
.call-number{font-size:17px;color:var(--ink);margin-top:3px}
.btn{display:flex;align-items:center;justify-content:space-between;border:1.5px solid var(--orange);border-radius:22px;color:var(--orange);font-family:"Open Sans",Arial,sans-serif;font-weight:600;font-size:13.5px;padding-left:20px;overflow:hidden;background:var(--white);white-space:nowrap}
.btn .go{width:40px;height:100%;background:var(--orange);display:flex;align-items:center;justify-content:center;flex:none}
.appointment{left:840px;top:28px;width:226px;height:42px;font-size:13px}
.nav{left:0;top:99px;width:1200px;height:53px;background:var(--green)}
.nav a{position:absolute;top:0;height:53px;line-height:53px;color:var(--white);font-family:"Open Sans",Arial,sans-serif;font-size:13px;text-decoration:none;text-align:center}
.nav a.active{background:var(--orange)}
.nav .sep{position:absolute;top:12px;width:1px;height:29px;background:rgba(255,255,255,.25)}
.brand-tab{left:513px;top:99px;width:174px;height:53px;background:var(--white);clip-path:polygon(0 0,100% 0,93% 100%,7% 100%)}
.brand{left:500px;top:12px;width:200px;text-align:center}
.brand-mark{width:80px;height:80px;border-radius:50%;background:var(--orange);margin:0 auto}
.brand-name{font-family:"Open Sans",Arial,sans-serif;font-size:22px;font-weight:600;color:var(--green-dark);margin-top:8px}

/* hero */
.hero{left:0;top:152px;width:1200px;height:513px;background:linear-gradient(90deg,#f4f3f1 0%,#ece9e6 35%,#d9dde3 55%,#eaeaea 75%,#f3f2f0 100%)}
.hero-title{left:110px;top:278px;width:430px;text-align:center;font-family:"Open Sans",Arial,sans-serif;font-weight:700;font-size:29px;letter-spacing:1.5px;line-height:49px;color:var(--ink)}
.hero-text{left:145px;top:390px;width:360px;text-align:center;font-size:14.5px;line-height:25px;color:var(--muted)}
.hero-btn{left:229px;top:481px;width:194px;height:40px}
.arrow{top:392px}

/* what we do */
.sec-title{left:0;width:1200px;text-align:center;font-family:"Open Sans",Arial,sans-serif;font-size:26px;font-weight:400;color:var(--ink)}
.sec-sub{left:0;width:1200px;text-align:center;font-size:12.5px;color:var(--muted)}
.cards{left:132px;top:840px;width:934px;height:214px;border:1px solid var(--line);display:flex}
.card{flex:1;border-left:1px solid var(--line);text-align:center;padding:76px 26px 0;position:relative}
.card:first-child{border-left:none;background:var(--green);color:var(--white)}
.card h3{font-family:"Open Sans",Arial,sans-serif;font-size:13.5px;font-weight:600;line-height:22px}
.card p{font-size:12px;line-height:21px;margin-top:8px;color:var(--muted)}
.card:first-child p{color:#eef3e4}
.card .more{position:absolute;left:0;right:0;bottom:8px;font-size:11px;line-height:14px;color:#999}
.card:first-child .more{color:#e0ead0}
.diamond{top:796px;width:76px;height:76px;background:var(--white);border:1px solid var(--line);transform:rotate(45deg)}
.diamond-icon{top:810px;width:48px;height:48px}

/* welcome */
.welcome{left:0;top:1111px;width:1200px;height:391px;background:var(--soft);border-top:1px solid #e6e6e6;border-bottom:1px solid #e6e6e6}
.welcome-photo{left:0;top:1111px;width:601px;height:391px;background:linear-gradient(90deg,#d9d6d3 0%,#e7e4e1 45%,#efeeec 80%,#f4f4f4 100%)}
.play{left:308px;top:1267px}
.welcome-title{left:625px;top:1162px;font-family:"Open Sans",Arial,sans-serif;font-size:25px;font-weight:400;color:var(--ink)}
.welcome-text{left:625px;top:1212px;width:450px;font-size:12px;line-height:21.5px;color:var(--muted)}
.welcome-text p+p{margin-top:21px}
.welcome-btn{left:625px;top:1387px;width:194px;height:40px}

/* services */
.services{left:132px;top:1631px;width:934px;display:flex;justify-content:space-between}
.service{width:222px;text-align:center}
.service-photo{width:174px;height:174px;border-radius:50%;border:6px solid var(--green-dark);margin:0 auto}
.service h3{font-family:"Open Sans",Arial,sans-serif;font-size:13.5px;font-weight:600;margin-top:24px}
.service p{font-size:12px;line-height:21.5px;color:var(--muted);margin-top:6px}
.service .more{display:block;font-size:10.5px;font-weight:700;color:var(--orange);margin-top:6px}
.svc-nav{left:1046px;top:1563px;font-size:13px;color:#999;letter-spacing:4px}

/* mailing list */
.mail-band{left:0;top:1995px;width:1200px;height:204px;background:linear-gradient(90deg,#33424a 0%,#3b4a51 45%,#4a5658 70%,#3a474d 100%)}
.mail-title{left:246px;top:2064px;font-family:"Open Sans",Arial,sans-serif;font-size:23px;font-weight:600;color:var(--white);letter-spacing:.5px}
.mail-sub{left:246px;top:2099px;font-family:"Open Sans",Arial,sans-serif;font-size:14px;color:#e3e6e7}
.mail-form{left:587px;top:2079px;width:466px;height:38px;background:var(--white);border-radius:20px;overflow:hidden;display:flex}
.mail-form span{flex:1;font-size:11.5px;color:#777;line-height:38px;padding-left:24px}
.mail-form b{width:112px;background:var(--orange);color:var(--white);font-family:"Open Sans",Arial,sans-serif;font-size:13px;font-weight:600;text-align:center;line-height:38px}

/* footer */
.f-brand{left:142px;top:2252px;width:200px;text-align:center}
.f-brand .brand-mark{width:86px;height:86px}
.f-brand .brand-name{font-size:24px;margin-top:10px}
.f-title{top:2232px;font-family:"Open Sans",Arial,sans-serif;font-size:15px;font-weight:600;color:var(--ink)}
.links{left:414px;top:2268px;list-style:none;font-size:12px;line-height:23px;color:#555}
.f-text{left:585px;top:2268px;width:240px;font-size:12px;line-height:19px;color:#555}
.f-input{left:585px;top:2313px;width:237px;height:33px;border:1px solid #ccc;font-size:11px;color:#999;line-height:31px;padding-left:12px}
.f-btn{left:580px;top:2356px;width:117px;height:37px;border:1.5px solid var(--orange);border-radius:20px;color:var(--orange);font-family:"Open Sans",Arial,sans-serif;font-size:13px;font-weight:600;text-align:center;line-height:34px}
.contact{left:917px;top:2272px;font-size:12px;line-height:20px;color:#555}
.contact li{list-style:none;display:flex;gap:14px;margin-bottom:10px}
.contact li svg{flex:none;margin-top:3px}
.rule{left:132px;top:2435px;width:934px;height:1px;background:var(--line)}
.copy{left:132px;top:2460px;font-size:11.5px;color:#555}
.follow{left:874px;top:2452px;display:flex;align-items:center;gap:8px;font-size:11.5px;color:#555}
.follow i{display:block;width:28px;height:28px;border:1.5px solid var(--orange);border-radius:50%;position:relative}
.follow i::after{content:"";position:absolute;left:8px;top:8px;width:9px;height:9px;border-radius:50%;background:var(--orange)}
</style>
</head>
<body>

<header>
  <div class="abs topline"></div>
  <div class="abs call">
    <svg width="40" height="40" viewBox="0 0 40 40" aria-hidden="true"><circle cx="20" cy="20" r="17" fill="none" stroke="#f7941d" stroke-width="2.5"/><path d="M14 12c1-1 2-1 3 0l2 3c.6 1 .3 1.8-.5 2.4l-1 .8c.8 2 2.3 3.5 4.3 4.3l.8-1c.6-.8 1.4-1.1 2.4-.5l3 2c1 1 1 2 0 3-3 3-8 1-11.5-2.5S11 15 14 12z" fill="#f7941d"/></svg>
    <div><div class="call-label">Call Us :</div><div class="call-number">+345-210-4476</div></div>
  </div>
  <div class="abs btn appointment">MAKE AN APPOINTMENT<span class="go"><svg width="14" height="14" viewBox="0 0 14 14"><circle cx="7" cy="7" r="6.5" fill="#fff"/><path d="M6 4l3 3-3 3" stroke="#f7941d" stroke-width="1.8" fill="none"/></svg></span></div>

  <nav class="abs nav">
    <a class="active" style="left:132px;width:97px">HOME</a>
    <span class="sep" style="left:229px"></span>
    <a style="left:236px;width:130px">ABOUT US</a>
    <span class="sep" style="left:366px"></span>
    <a style="left:366px;width:130px">SERVICES</a>
    <a style="left:710px;width:158px">ASSISTED LIVING</a>
    <span class="sep" style="left:868px"></span>
    <a style="left:868px;width:116px">BLOG</a>
    <span class="sep" style="left:984px"></span>
    <a style="left:984px;width:110px">CONTACT</a>
  </nav>
  <div class="abs brand-tab"></div>
  <div class="abs brand"><div class="brand-mark"></div><div class="brand-name">Vellisant</div></div>
</header>

<section>
  <div class="abs hero" role="img" aria-label="Photo of a smiling nurse in blue scrubs holding the hands of an elderly woman in a white robe"></div>
  <h1 class="abs hero-title">HOME AND COMMUNITY<br>BASED SERVICES</h1>
  <p class="abs hero-text">Aliquip ex ea commodo consequat.. Duis aute irure dolor in reprehenderit in voluptate velit esse cillum dolore eu fugiat nulla pariatur...</p>
  <div class="abs btn hero-btn">LEARN MORE INFO<span class="go"><svg width="14" height="14" viewBox="0 0 14 14"><circle cx="7" cy="7" r="6.5" fill="#fff"/><path d="M6 4l3 3-3 3" stroke="#f7941d" stroke-width="1.8" fill="none"/></svg></span></div>
  <svg class="abs arrow" style="left:86px" width="24" height="76" viewBox="0 0 24 76" aria-hidden="true"><path d="M22 2L2 38l20 36" fill="none" stroke="#999" stroke-width="1.5"/></svg>
  <svg class="abs arrow" style="left:1090px" width="24" height="76" viewBox="0 0 24 76" aria-hidden="true"><path d="M2 2l20 36L2 74" fill="none" stroke="#999" stroke-width="1.5"/></svg>
</section>

<section>
  <h2 class="abs sec-title" style="top:706px">WHAT WE DO</h2>
  <p class="abs sec-sub" style="top:744px">Lorem ipsum dolor sit amet, consectetur adipiscing elit, sed do eiusmod tempor incididunt ut labore...</p>
  <div class="abs cards">
    <div class="card"><h3>Comprehensive Primary Care<br>Services</h3><p>Aliquip ex ea commodo consequat. Duis aute irure dolor in reprehenderit in voluptate velit esse cillum dolore pariatur...</p><span class="more">↘</span></div>
    <div class="card"><h3>Reduce Health Care Delivery<br>Gap</h3><p>Aliquip ex ea commodo consequat. Duis aute irure dolor in reprehenderit in voluptate velit esse cillum dolore pariatur...</p><span class="more">↘</span></div>
    <div class="card"><h3>High Quality Healthcare at Your<br>Door</h3><p>Aliquip ex ea commodo consequat. Duis aute irure dolor in reprehenderit in voluptate velit esse cillum dolore pariatur...</p><span class="more">↘</span></div>
  </div>
  <div class="abs diamond" style="left:253px"></div>
  <div class="abs diamond" style="left:564px"></div>
  <div class="abs diamond" style="left:875px"></div>
  <svg class="abs diamond-icon" style="left:267px" viewBox="0 0 48 48" aria-hidden="true"><rect x="18" y="9" width="12" height="6" rx="1.5" fill="none" stroke="#5b8113" stroke-width="3"/><rect x="7" y="14" width="34" height="25" rx="3" fill="#5b8113"/><path d="M24 19v15M16.5 26.5h15" stroke="#fff" stroke-width="4"/></svg>
  <svg class="abs diamond-icon" style="left:578px" viewBox="0 0 48 48" aria-hidden="true"><path d="M12 8v10a8 8 0 0016 0V8" fill="none" stroke="#5b8113" stroke-width="3.5"/><path d="M20 26v6a8 8 0 0016 0v-6" fill="none" stroke="#5b8113" stroke-width="3.5"/><circle cx="36" cy="22" r="4.5" fill="none" stroke="#5b8113" stroke-width="3"/></svg>
  <svg class="abs diamond-icon" style="left:889px" viewBox="0 0 48 48" aria-hidden="true"><path d="M24 8L6 24h5v16h10V30h6v10h10V24h5z" fill="#5b8113"/></svg>
</section>

<section>
  <div class="abs welcome"></div>
  <div class="abs welcome-photo" role="img" aria-label="Photo of a young woman helping an elderly woman walk with crutches indoors"></div>
  <svg class="abs play" width="80" height="80" viewBox="0 0 80 80" aria-label="Play video"><circle cx="40" cy="40" r="37" fill="rgba(40,40,40,.75)" stroke="#fff" stroke-width="3"/><path d="M32 25l24 15-24 15z" fill="#fff"/></svg>
  <h2 class="abs welcome-title">WELCOME TO VELLISANT</h2>
  <div class="abs welcome-text">
    <p>Vellisant offers home and Community Based Services for adults who wish to continue to live independently in the comfort of their communities.</p>
    <p>We provide on site services and deliver high quality healthcare at your door. Our experienced physicians coordinate care with our certified nurse practitioners and provide chronic care management, physical therapy, rehabilitation and medications management.</p>
  </div>
  <div class="abs btn welcome-btn">LEARN MORE INFO<span class="go"><svg width="14" height="14" viewBox="0 0 14 14"><circle cx="7" cy="7" r="6.5" fill="#fff"/><path d="M6 4l3 3-3 3" stroke="#f7941d" stroke-width="1.8" fill="none"/></svg></span></div>
</section>

<section>
  <h2 class="abs sec-title" style="top:1554px">SERVICES</h2>
  <p class="abs sec-sub" style="top:1593px">Lorem ipsum dolor sit amet, consectetur adipiscing elit, sed do eiusmod tempor incididunt ut labore</p>
  <div class="abs svc-nav">‹ ›</div>
  <div class="abs services">
    <div class="service"><div class="service-photo" role="img" aria-label="Photo of a caregiver embracing an elderly woman at home" style="background:linear-gradient(135deg,#e9ddd2,#c9b6a6 60%,#5f86b8)"></div><h3>HOME HEALTH ASSISTANCE</h3><p>Lorem ipsum dolor sit amet, consectetur adipiscing elit, sed do eiusmod tempor incididunt ut labore...</p><span class="more">LEARN MORE &gt;&gt;</span></div>
    <div class="service"><div class="service-photo" role="img" aria-label="Photo of a therapist guiding an elderly man through physical therapy exercise" style="background:linear-gradient(135deg,#c5c9cc,#8e969c 55%,#d6d6d4)"></div><h3>PHYSICAL THERAPY</h3><p>Lorem ipsum dolor sit amet, consectetur adipiscing elit, sed do eiusmod tempor incididunt ut labore...</p><span class="more">LEARN MORE &gt;&gt;</span></div>
    <div class="service"><div class="service-photo" role="img" aria-label="Illustration of a glowing brain in blue and pink light" style="background:radial-gradient(circle,#c0609a,#3b3f9a 55%,#101a4a)"></div><h3>MENTAL HEALTH</h3><p>Lorem ipsum dolor sit amet, consectetur adipiscing elit, sed do eiusmod tempor incididunt ut labore...</p><span class="more">LEARN MORE &gt;&gt;</span></div>
    <div class="service"><div class="service-photo" role="img" aria-label="Photo of an elderly man smiling during a dental checkup" style="background:linear-gradient(135deg,#dfe6ea,#c8bfb5 55%,#e9ecee)"></div><h3>DENTAL HEALTH</h3><p>Lorem ipsum dolor sit amet, consectetur adipiscing elit, sed do eiusmod tempor incididunt ut labore...</p><span class="more">LEARN MORE &gt;&gt;</span></div>
  </div>
</section>

<section>
  <div class="abs mail-band" role="img" aria-label="Dimmed photo of an elderly couple smiling together"></div>
  <svg class="abs" style="left:130px;top:2050px" width="106" height="70" viewBox="0 0 106 70" aria-hidden="true"><rect x="4" y="14" width="58" height="40" rx="3" fill="none" stroke="rgba(255,255,255,.25)" stroke-width="3" transform="rotate(-12 33 34)"/><path d="M10 20l25 16 22-22" fill="none" stroke="rgba(255,255,255,.25)" stroke-width="3"/><path d="M62 28l36-16-10 36-9-10-6 8v-11z" fill="none" stroke="#fff" stroke-width="2.5" stroke-linejoin="round"/><path d="M79 38l19-26" stroke="#fff" stroke-width="2"/></svg>
  <h2 class="abs mail-title">JOIN MAILING LIST</h2>
  <p class="abs mail-sub">Subscribe to receive updates &amp; exclusive offers.</p>
  <div class="abs mail-form"><span>Enter your E - mail</span><b>SUBSCRIBE</b></div>
</section>

<footer>
  <div class="abs f-brand"><div class="brand-mark"></div><div class="brand-name">Vellisant</div></div>

  <h3 class="abs f-title" style="left:414px">Quick Links</h3>
  <ul class="abs links"><li>Home</li><li>About us</li><li>Services</li><li>Assisted Living</li><li>Blog</li><li>Contact</li></ul>

  <h3 class="abs f-title" style="left:585px">Newsletter Subscription</h3>
  <p class="abs f-text">Register your Email Address to get Information about us</p>
  <div class="abs f-input">Email Address</div>
  <div class="abs f-btn">SUBSCRIBE</div>

  <h3 class="abs f-title" style="left:917px">Contact Us</h3>
  <ul class="abs contact">
    <li><svg width="12" height="15" viewBox="0 0 12 15"><path d="M6 0a6 6 0 00-6 6c0 4 6 9 6 9s6-5 6-9a6 6 0 00-6-6z" fill="#f7941d"/><circle cx="6" cy="6" r="2.2" fill="#fff"/></svg><span style="text-align:right">Box 51870 Vellisant,<br>Elmwood Lane, City-4620</span></li>
    <li><svg width="12" height="13" viewBox="0 0 12 13"><path d="M2 1c1-1 2 0 2.5.7l1 1.7c.4.7 0 1.2-.5 1.6l-.6.5c.6 1.3 1.6 2.3 2.9 2.9l.5-.6c.4-.5.9-.9 1.6-.5l1.7 1c.7.5 1.7 1.5.7 2.5-2 2-5 0-7-2S0 3 2 1z" fill="#f7941d"/></svg><span>1 800 555 0147</span></li>
    <li style="margin-top:8px"><svg width="14" height="11" viewBox="0 0 14 11"><rect width="14" height="11" rx="1.5" fill="#f7941d"/><path d="M1 1.5l6 4.5 6-4.5" fill="none" stroke="#fff" stroke-width="1.3"/></svg><span>info@vellisant.com</span></li>
  </ul>

  <div class="abs rule"></div>
  <p class="abs copy">Copyright © 2017, Vellisant. All rights reserved.</p>
  <div class="abs follow">Follow Us :<i></i><i></i><i></i><i></i></div>
</footer>

</body>
</html>
```